Drone service provider needs a brilliant web design

I need a responsive web design for a new drone service company. Pelham Drone Solutions provides turnkey solutions to capture, process, and deliver actionable aerial data to customers. The design should communicate a professional company that is safe, legal and insured. I included our logo design and business card designs for reference.
*content to be supplied after design selected

Target Market(s)

We serve telecommunications, construction, government, utility infrastructure, insurance and other industries.

Industry/Entity Type

Industrial

Number of Pages Required

5+ page

Colors

Designer to choose colors to be used in the design.

Requirements
Must have
• The design should highlight professional services to include Inspections, Mapping, Consulting and Training. The site should include aerial images and video to compliment the services offered. The landing page must include following sections in order: HOME, SERVICES, ABOUT, DEMO REEL, CLIENTS, CONTACT FORM, and social media buttons (Facebook, LinkedIn, Twitter, YouTube, Instagram). Contact: 615-382-9041 info@pelhamdronesolutions-example.com Smyrna, TN
• Sitemap:
• 6 pages: Home, Inspections, Mapping, Training, Consulting, About
• HOME (Landing Page)
• • Header with logo and tab links (Home, Services, About, Contact)
• • 'CAPTURE. PROCESS. DELIVER.' tagline and 'CONTACT US' button displayed within aerial image of drone over city or construction site
• • Services section with icons, text and read more link to page
• • About section with photo and text with three icons for SAFE. LEGAL. INSURED.
• • Demo reel
• • Clients logos shown scrolling horizontally
• • Contact form
• • Footer with logo, phone, email, social media buttons
• SERVICES (4 different pages)
• • Inspections
• • Mapping
• • Consulting
• • Training
• ABOUT page
• • Company
• • Partners
• • Certifications & Associations
• • Careers
• CONTACT linked to bottom of landing page
• Would you like to receive the newsletter? Yes or No Drop-down list
Nice to have
• Photos of KVR Marlin or Corvex inspecting infrastructure, buildings, construction sites, etc. A photo of one or two pilots in vest and helmet. Free stock photos preferred but would purchase the right photo that's more relevant.
• website references:
• https://www.quillrotor-example.com/
• https://www.brentfieldworks-example.com/services
• https://www.tomaro-example.com/
• http://gantrymetric-example.com/
• http://lumbrook-example.com/
• http://fennotics-example.com/
• https://www.grebe-example.io/
Should not have
• not an aerial photography or videography service business, no blog or newsletter

```html
<!DOCTYPE html>
<html lang="en">
<head>
<meta charset="utf-8">
<title>Inspections | Pelham Drone Solutions</title>
<link rel="stylesheet" href="https://fonts.googleapis.com/css2?family=Montserrat:wght@500;600;700;800&family=Open+Sans:wght@400;600&display=swap">
<style>
:root{
  --blue:#1b8fd3;
  --blue-dark:#1476b3;
  --ink:#2a2f36;
  --text:#6b7079;
  --white:#ffffff;
  --footer:#262a2f;
  --footer-line:#4a4f56;
}
*{box-sizing:border-box;margin:0;padding:0}
html,body{width:1200px;height:2852px;overflow:hidden}
body{font-family:"Open Sans",Arial,sans-serif;color:var(--text);background:var(--white);position:relative}
.heading{font-family:"Montserrat",Arial,sans-serif}

/* Hero */
.hero{position:absolute;left:0;top:0;width:1200px;height:400px;
  background:linear-gradient(180deg,#4c5866 0%,#7a8796 40%,#5c6b7a 75%,#3e4a57 100%)}
.hero-top{position:absolute;left:0;top:0;width:1200px;height:120px;background:rgba(20,30,45,.55)}
.nav{position:absolute;left:96px;top:48px;display:flex;gap:40px;list-style:none}
.nav a{font-family:"Montserrat",Arial,sans-serif;font-weight:600;font-size:15px;color:var(--white);text-decoration:none;letter-spacing:.5px}
.logo-tab{position:absolute;left:420px;top:0;width:360px;height:150px}
.logo-name{position:absolute;left:420px;top:34px;width:360px;text-align:center;font-family:"Montserrat",Arial,sans-serif;font-weight:800;font-size:26px;line-height:1.15;color:var(--ink);letter-spacing:1px}
.social{position:absolute;right:100px;top:38px;display:flex;gap:10px}
.social span{width:34px;height:34px;border:2px solid var(--white);border-radius:6px;display:block}
.hero-title{position:absolute;left:96px;top:250px;font-family:"Montserrat",Arial,sans-serif;font-weight:800;font-size:68px;color:var(--white);letter-spacing:1px}

/* Intro */
.intro{position:absolute;left:0;top:400px;width:1200px;height:240px;text-align:center}
.intro h2{margin-top:84px;font-size:28px;font-weight:700;color:var(--blue);letter-spacing:1px}
.intro h2::after{content:"";display:block;width:70px;height:3px;background:var(--blue);margin:10px auto 0}
.intro p{width:820px;margin:18px auto 0;font-size:14px;line-height:1.7}

/* Service rows */
.service{position:absolute;left:0;width:1200px}
.service .photo{position:absolute;top:0;height:100%}
.service .copy{position:absolute;top:70px;width:580px}
.service h3{font-family:"Montserrat",Arial,sans-serif;font-weight:700;font-size:28px;color:var(--blue)}
.service h4{font-family:"Montserrat",Arial,sans-serif;font-weight:600;font-size:17px;color:var(--ink);margin:4px 0 18px}
.service p{font-size:13.5px;line-height:1.75;margin-bottom:16px}
.service.light{background:var(--white)}
.service.dark{background:var(--blue);clip-path:polygon(0 50px,100% 0,100% 100%,0 100%)}
.service.dark h3,.service.dark h4,.service.dark p{color:var(--white)}
.photo-right{right:0;width:500px;clip-path:polygon(16% 8%,100% 0,100% 100%,0 92%)}
.photo-left{left:0;width:520px;clip-path:polygon(0 10%,100% 0,86% 100%,0 100%)}

.power{top:640px;height:440px}
.power .photo{background:linear-gradient(160deg,#9fb4c6,#6f7f8c 55%,#c4a64a)}
.power .copy{left:100px}
.infra{top:1060px;height:470px;z-index:2}
.infra .photo{background:linear-gradient(180deg,#8a5a38 0%,#c9b79b 40%,#e8ecee 70%,#5d6b55 100%)}
.infra .copy{left:540px;top:110px;width:560px}
.cell{top:1530px;height:440px}
.cell .photo{background:linear-gradient(180deg,#a9bccd 0%,#c8cfd4 45%,#6b7a5a 100%)}
.cell .copy{left:100px}
.roof{top:1950px;height:490px;z-index:2}
.roof .photo{background:linear-gradient(170deg,#a8c3d6 0%,#8a8f96 50%,#4d5258 100%)}
.roof .copy{left:540px;top:110px;width:560px}

/* Footer */
.footer{position:absolute;left:0;top:2420px;width:1200px;height:432px;background:var(--footer);color:var(--white)}
.footer-logo{position:absolute;top:70px;width:1200px;text-align:center;font-family:"Montserrat",Arial,sans-serif;font-weight:800;font-size:26px;letter-spacing:1px;color:var(--white)}
.contact{position:absolute;top:150px;width:1200px;display:flex;justify-content:center;gap:60px;font-size:16px}
.contact div{display:flex;align-items:center;gap:12px}
.contact svg{width:38px;height:38px}
.footer-nav{position:absolute;top:238px;left:300px;width:600px;display:flex;justify-content:space-between;list-style:none}
.footer-nav a{font-family:"Montserrat",Arial,sans-serif;font-weight:600;font-size:14px;color:var(--white);text-decoration:none}
.footer-nav li.sep{color:var(--footer-line)}
.rule{position:absolute;top:290px;left:96px;width:1008px;height:1px;background:var(--footer-line)}
.copyright{position:absolute;top:318px;left:96px;font-size:13px}
.footer-social{position:absolute;top:308px;right:96px;display:flex;gap:10px}
.footer-social span{width:30px;height:30px;border:2px solid var(--white);border-radius:50%;display:block}
</style>
</head>
<body>

<header class="hero">
  <div class="hero-top"></div>
  <div class="hero-photo" role="img" aria-label="Aerial view of a drone flying over a city and harbour" style="position:absolute;inset:0"></div>
  <ul class="nav">
    <li><a href="#">HOME</a></li>
    <li><a href="#">SERVICES</a></li>
    <li><a href="#">ABOUT</a></li>
  </ul>
  <svg class="logo-tab" viewBox="0 0 360 150" aria-hidden="true">
    <path d="M0 0 H360 L330 118 Q320 140 296 140 H64 Q40 140 30 118 Z" fill="#1b8fd3"/>
    <path d="M14 0 H346 L320 104 Q312 124 290 124 H70 Q48 124 40 104 Z" fill="#ffffff"/>
  </svg>
  <div class="logo-name">PELHAM<br><span style="font-size:13px;letter-spacing:3px">DRONE SOLUTIONS</span></div>
  <div class="social" aria-label="Social media links">
    <span></span><span></span><span></span><span></span><span></span>
  </div>
  <h1 class="hero-title">INSPECTIONS</h1>
</header>

<section class="intro">
  <h2 class="heading">INSPECTIONS</h2>
  <p>Nam libero tempore, cum soluta nobis est eligendi optio cumque nihil impedit quo minus id quod maxime placeat facere possimus, omnis voluptas assumenda est, omnis dolor repellendus.</p>
</section>

<section class="service light power">
  <div class="copy">
    <h3>Power Utilities</h3>
    <h4>(solar, wind, power plants, power lines)</h4>
    <p>Nemo enim ipsam voluptatem quia voluptas sit aspernatur aut odit aut fugit, sed quia consequuntur magni dolores eos qui ratione voluptatem sequi nesciunt. Neque porro quisquam est, qui dolorem ipsum quia dolor sit amet, consectetur, adipisci velit, sed quia non numquam eius modi tempora incidunt ut labore et dolore magnam aliquam quaerat voluptatem.</p>
    <p>Quis autem vel eum iure reprehenderit qui in ea voluptate velit esse quam nihil molestiae consequatur, vel illum qui dolorem eum fugiat quo voluptas nulla pariatur, at vero eos et accusamus et iusto odio dignissimos ducimus qui blanditiis.</p>
  </div>
  <div class="photo photo-right" role="img" aria-label="Workers in safety helmets inspecting an electrical substation"></div>
</section>

<section class="service dark infra">
  <div class="photo photo-left" role="img" aria-label="Water flowing over a large dam spillway"></div>
  <div class="copy">
    <h3>Infrastructure</h3>
    <h4>(bridges, dams, railways, roads)</h4>
    <p>Nemo enim ipsam voluptatem quia voluptas sit aspernatur aut odit aut fugit, sed quia consequuntur magni dolores eos qui ratione voluptatem sequi nesciunt. Neque porro quisquam est, qui dolorem ipsum quia dolor sit amet, consectetur, adipisci velit, sed quia non numquam eius modi tempora incidunt ut labore et dolore magnam aliquam quaerat voluptatem.</p>
    <p>Quis autem vel eum iure reprehenderit qui in ea voluptate velit esse quam nihil molestiae consequatur, vel illum qui dolorem eum fugiat quo voluptas nulla pariatur, at vero eos et accusamus et iusto odio dignissimos ducimus qui blanditiis.</p>
  </div>
</section>

<section class="service light cell">
  <div class="copy">
    <h3>Cellular Tower</h3>
    <h4>Nemo enim ipsam voluptatem quia voluptas</h4>
    <p>Nemo enim ipsam voluptatem quia voluptas sit aspernatur aut odit aut fugit, sed quia consequuntur magni dolores eos qui ratione voluptatem sequi nesciunt. Neque porro quisquam est, qui dolorem ipsum quia dolor sit amet, consectetur, adipisci velit, sed quia non numquam eius modi tempora incidunt ut labore et dolore magnam aliquam quaerat voluptatem.</p>
    <p>Quis autem vel eum iure reprehenderit qui in ea voluptate velit esse quam nihil molestiae consequatur, vel illum qui dolorem eum fugiat quo voluptas nulla pariatur, at vero eos et accusamus et iusto odio dignissimos ducimus qui blanditiis.</p>
  </div>
  <div class="photo photo-right" role="img" aria-label="Red and white cellular tower against hills and sky"></div>
</section>

<section class="service dark roof">
  <div class="photo photo-left" role="img" aria-label="House roof seen from below against a blue sky"></div>
  <div class="copy">
    <h3>Roof</h3>
    <h4>Nemo enim ipsam voluptatem quia voluptas</h4>
    <p>Nemo enim ipsam voluptatem quia voluptas sit aspernatur aut odit aut fugit, sed quia consequuntur magni dolores eos qui ratione voluptatem sequi nesciunt. Neque porro quisquam est, qui dolorem ipsum quia dolor sit amet, consectetur, adipisci velit, sed quia non numquam eius modi tempora incidunt ut labore et dolore magnam aliquam quaerat voluptatem.</p>
    <p>Quis autem vel eum iure reprehenderit qui in ea voluptate velit esse quam nihil molestiae consequatur, vel illum qui dolorem eum fugiat quo voluptas nulla pariatur, at vero eos et accusamus et iusto odio dignissimos ducimus qui blanditiis.</p>
  </div>
</section>

<footer class="footer">
  <div class="footer-logo">PELHAM<br><span style="font-size:13px;letter-spacing:3px">DRONE SOLUTIONS</span></div>
  <div class="contact">
    <div>
      <svg viewBox="0 0 38 38" aria-hidden="true"><circle cx="19" cy="19" r="17" fill="none" stroke="#fff" stroke-width="2"/><rect x="11" y="13" width="16" height="12" fill="none" stroke="#fff" stroke-width="1.8"/><path d="M11 13 L19 20 L27 13" fill="none" stroke="#fff" stroke-width="1.8"/></svg>
      <span>info@pelhamdronesolutions-example.com</span>
    </div>
    <div>
      <svg viewBox="0 0 38 38" aria-hidden="true"><circle cx="19" cy="19" r="17" fill="none" stroke="#fff" stroke-width="2"/><path d="M13 11 L16 11 L18 16 L16 18 Q18 22 21 23 L23 21 L28 23 L28 26 Q27 28 24 28 Q12 26 10 14 Q10 11 13 11 Z" fill="#fff"/></svg>
      <span>615-382-9041</span>
    </div>
  </div>
  <ul class="footer-nav">
    <li><a href="#">HOME</a></li><li class="sep">|</li>
    <li><a href="#">SERVICES</a></li><li class="sep">|</li>
    <li><a href="#">ABOUT</a></li><li class="sep">|</li>
    <li><a href="#">CONTACT US</a></li>
  </ul>
  <div class="rule"></div>
  <p class="copyright">Copyright © 2018 Pelham Drone Solutions. All Right Reserved.</p>
  <div class="footer-social" aria-label="Social media links">
    <span></span><span></span><span></span><span></span><span></span>
  </div>
</footer>

</body>
</html>
```